Business Card Design for Training Business

Clear Path Coaching is a new business that delivers training and other services with a focus on topics related to mental health and wellbeing, for example, Wellmind Response Course, Resilience etc. We have a strong focus on evidence-based psychology and neuroscience. I have a logo which I will upload with the brief, so please consider colours that work well with the logo.
Target Market(s)
Adults, workplaces (particularly government and not-for-profits)
Industry/Entity Type
Business
Contact Information for Business Card
Head Strong TrainingSamantha SellwoodDirector0438 770 850sam@headstrongtraining.com.auwww.headstrongtraining.com.au

```html
<!DOCTYPE html>
<html lang="en">
<head>
<meta charset="utf-8">
<title>Clear Path Coaching – Business Card</title>
<link href="https://fonts.googleapis.com/css2?family=Arimo:wght@400;700&display=swap" rel="stylesheet">
<style>
  :root {
    --backdrop: #d9d8d6;
    --card: #1b1b1d;
    --teal: #2db4bc;
    --teal-deep: #1d6a69;
    --logo-grey: #a4a4a6;
    --text-light: #f2f2f2;
  }
  * { margin: 0; padding: 0; box-sizing: border-box; }
  html, body {
    width: 1200px;
    height: 787px;
    overflow: hidden;
    background: var(--backdrop);
    font-family: "Arimo", Arial, sans-serif;
  }
  .sheet {
    position: relative;
    width: 1200px;
    height: 787px;
    display: flex;
    align-items: center;
    justify-content: center;
    gap: 40px;
  }
  .card {
    position: relative;
    width: 540px;
    height: 309px;
    background: var(--card);
    border-radius: 4px;
    box-shadow: 0 10px 28px rgba(0,0,0,0.25);
    overflow: hidden;
  }

  /* Back of card */
  .card-back .brand {
    position: absolute;
    top: 92px;
    left: 0;
    width: 100%;
    display: flex;
    flex-direction: column;
    align-items: center;
    gap: 14px;
  }
  .brand-dot {
    width: 58px;
    height: 58px;
    border-radius: 50%;
    border: 2px solid var(--teal);
  }
  .brand-name {
    color: var(--logo-grey);
    font-weight: 400;
    font-size: 17px;
    letter-spacing: 0.18em;
    text-transform: uppercase;
    white-space: nowrap;
  }
  .card-back .web {
    position: absolute;
    left: 38px;
    bottom: 34px;
    color: var(--text-light);
    font-size: 13px;
    letter-spacing: 0.02em;
  }

  /* Front of card */
  .card-front .brand {
    position: absolute;
    top: 30px;
    left: 52px;
    display: flex;
    align-items: center;
    gap: 10px;
  }
  .card-front .brand-dot {
    width: 34px;
    height: 34px;
  }
  .card-front .brand-name { font-size: 15px; }
  .person {
    position: absolute;
    top: 108px;
    left: 52px;
  }
  .person-name {
    color: var(--teal);
    font-weight: 700;
    font-size: 22px;
    line-height: 1.1;
  }
  .person-role {
    color: var(--text-light);
    font-size: 13px;
    margin-top: 4px;
  }
  .contact {
    position: absolute;
    top: 178px;
    left: 52px;
    list-style: none;
    display: flex;
    flex-direction: column;
    gap: 9px;
  }
  .contact li {
    display: flex;
    align-items: center;
    gap: 12px;
    color: var(--text-light);
    font-size: 13px;
  }
  .contact svg { width: 14px; height: 14px; flex: none; fill: var(--teal); }
  .emblem-area {
    position: absolute;
    right: -30px;
    top: 55px;
    width: 270px;
    height: 270px;
    border-radius: 50%;
    background: radial-gradient(circle, #141617 0%, #1c3b3b 55%, var(--teal-deep) 72%, rgba(29,106,105,0) 74%);
    opacity: 0.85;
  }
</style>
</head>
<body>
<main class="sheet">

  <section class="card card-back" aria-label="Card back">
    <div class="brand">
      <span class="brand-dot"></span>
      <span class="brand-name">Clear Path Coaching</span>
    </div>
    <p class="web">www.clearpathcoaching.example.au</p>
  </section>

  <section class="card card-front" aria-label="Card front">
    <div class="emblem-area" role="img" aria-label="Large decorative brand emblem in teal on dark ground"></div>

    <div class="brand">
      <span class="brand-dot"></span>
      <span class="brand-name">Clear Path Coaching</span>
    </div>

    <div class="person">
      <h1 class="person-name">Rebecca Tanfield</h1>
      <p class="person-role">Director</p>
    </div>

    <ul class="contact">
      <li>
        <svg viewBox="0 0 24 24" aria-hidden="true"><path d="M6.6 10.8a15.1 15.1 0 0 0 6.6 6.6l2.2-2.2c.3-.3.7-.4 1-.2 1.1.4 2.3.6 3.6.6.6 0 1 .4 1 1V20c0 .6-.4 1-1 1A17 17 0 0 1 3 4c0-.6.4-1 1-1h3.5c.6 0 1 .4 1 1 0 1.2.2 2.4.6 3.6.1.3 0 .7-.2 1z"/></svg>
        <span>0491 362 517</span>
      </li>
      <li>
        <svg viewBox="0 0 24 24" aria-hidden="true"><path d="M2 5h20v14H2z M2 5l10 8 10-8" fill="none" stroke="#2db4bc" stroke-width="2"/><path d="M3 6l9 7 9-7v12H3z"/></svg>
        <span>bec@clearpathcoaching.example.au</span>
      </li>
      <li>
        <svg viewBox="0 0 24 24" aria-hidden="true"><circle cx="12" cy="12" r="10"/><circle cx="12" cy="9" r="3" fill="#1b1b1d"/><path d="M6.5 17.5a6.5 6.5 0 0 1 11 0" fill="#1b1b1d"/></svg>
        <span>www.clearpathcoaching.example.au</span>
      </li>
    </ul>
  </section>

</main>
</body>
</html>
```